Harrowgate Care Assurance Ltd needs a business card and logo

We need a logo for documents, invoices etc and a business card to match. We are a health auditing, training and consulting company based in NZ and working in both Australia and NZ. We ensure health organisations meet all their compliance requirements and develop expertise in the health auditing sector. The design should in some way reflect either symbols for quality management in the health sector.

Target Market(s)

Health providers and those wishing to increase their capability in meeting and understanding compliance requirements

Industry/Entity Type

Business

Contact Information for Business Card

Logo plus contact details

Logo Text

Health auditing, consultancy and training

Requirements
Must have
• Name and contact details director: Marla Fenwick, mfenwick@hca-example.co.nz, PO Box 318, Warkworth, NZ, cell +6427391652

```html
<!DOCTYPE html>
<html lang="en">
<head>
<meta charset="utf-8">
<title>Harrowgate Care Assurance Ltd — Business Card</title>
<link rel="stylesheet" href="https://fonts.googleapis.com/css2?family=Didact+Gothic&family=Montserrat:wght@600&display=swap">
<style>
  :root {
    --backdrop: #2b2b2b;
    --card-white: #ffffff;
    --card-shade: #f1f2f2;
    --brand-green: #5a9179;
    --brand-green-light: #7db39c;
    --ink-dark: #2a2a2a;
    --ink-light: #ffffff;
  }
  * { box-sizing: border-box; margin: 0; padding: 0; }
  html, body {
    width: 1200px;
    height: 900px;
    overflow: hidden;
    background: var(--backdrop);
  }
  .canvas {
    position: relative;
    width: 1200px;
    height: 900px;
    display: flex;
    flex-direction: column;
    align-items: center;
    justify-content: center;
    gap: 40px;
  }
  .card {
    position: relative;
    width: 700px;
    height: 400px;
    background: linear-gradient(180deg, var(--card-white) 0%, var(--card-shade) 100%);
    overflow: hidden;
  }
  .brand {
    position: absolute;
    display: flex;
    align-items: center;
    gap: 22px;
  }
  .brand-mark {
    width: 62px;
    height: 62px;
    background: var(--brand-green);
    flex: none;
  }
  .brand-name {
    font-family: "Didact Gothic", sans-serif;
    font-weight: 400;
    color: var(--ink-dark);
    font-size: 40px;
    line-height: 1.05;
    letter-spacing: 0.5px;
  }
  .card--back .brand {
    left: 50%;
    top: 50%;
    transform: translate(-50%, -50%);
  }
  .card--front .brand {
    left: 150px;
    top: 58px;
  }
  .contact-band {
    position: absolute;
    left: 0;
    right: 0;
    bottom: 0;
    height: 170px;
    background: var(--brand-green);
    color: var(--ink-light);
    font-family: "Didact Gothic", sans-serif;
  }
  .contact-band::after {
    content: "";
    position: absolute;
    left: 0;
    right: 0;
    bottom: 0;
    height: 24px;
    background: var(--brand-green-light);
  }
  .holder {
    position: absolute;
    left: 44px;
    top: 62px;
  }
  .holder-name {
    font-family: "Montserrat", sans-serif;
    font-weight: 600;
    font-size: 21px;
    letter-spacing: 1px;
    text-transform: uppercase;
  }
  .holder-address {
    font-size: 18px;
    margin-top: 4px;
  }
  .reach {
    position: absolute;
    left: 400px;
    top: 18px;
    font-size: 18px;
    line-height: 1.35;
  }
  .reach dt { display: inline-block; width: 34px; }
  .reach dd { display: inline; }
</style>
</head>
<body>
<main class="canvas">
  <section class="card card--back" aria-label="Card back">
    <div class="brand">
      <span class="brand-mark" aria-hidden="true"></span>
      <p class="brand-name">Harrowgate Care<br>Assurance Ltd</p>
    </div>
  </section>

  <section class="card card--front" aria-label="Card front">
    <div class="brand">
      <span class="brand-mark" aria-hidden="true"></span>
      <p class="brand-name">Harrowgate Care<br>Assurance Ltd</p>
    </div>
    <div class="contact-band">
      <div class="holder">
        <p class="holder-name">Marla Fenwick</p>
        <p class="holder-address">PO Box 318, Warkworth, NZ</p>
      </div>
      <dl class="reach">
        <div><dt>M:</dt><dd>+6427391652</dd></div>
        <div><dt>E:</dt><dd>mfenwick@hca-example.co.nz</dd></div>
      </dl>
    </div>
  </section>
</main>
</body>
</html>
```